HOT TUB - SPAS service needs an business card

I need an business for my company who his specialise in a maintenance,water treatment and cleaning of Hot Tub - Spas for commercial and residential customers. The company operate mainly in the ski resort of Chamonix, Megève and St Gervais. The final product should communicate pure water, cleanest and professional for luxury property's.
I have upload a logo but any improvement on it is welcome.(color,size, details etc..) or any other idea. Thank you
Company Name: 58 BAINS
My name: Lucien Marchetti
Email: lucimarch@examplemail.net
Tel: +33 (0)6 71 58 29 64
Description to be on the card in french(first langage) and in English:
- Spas service
- Entretien, traitement eau, nettoyage.
- Maintenance, water treatment, cleaning.
Industry/Entity Type
Residential
Colors
Designer to choose colors to be used in the design.
Look and feel
Each slider illustrates characteristics of the customer's brand and the style your logo design should communicate.

```html
<!DOCTYPE html>
<html lang="fr">
<head>
<meta charset="utf-8">
<title>58 BAINS – Cartes de visite</title>
<link rel="stylesheet" href="https://fonts.googleapis.com/css2?family=Source+Sans+3:wght@400;600;700&display=swap">
<style>
  :root {
    --page: #eef1f4;
    --card: #22a3f4;
    --band: #0f63cf;
    --rule: #9ad8ff;
    --art: #3cb0f6;
    --ink: #ffffff;
  }
  * { margin: 0; padding: 0; box-sizing: border-box; }
  html, body {
    width: 1200px; height: 1134px; overflow: hidden;
    background: var(--page);
    font-family: "Source Sans 3", "Myriad Pro", Arial, sans-serif;
    color: var(--ink);
  }
  .canvas { position: relative; width: 1200px; height: 1134px; }
  .card {
    position: absolute; width: 888px; height: 506px;
    background: var(--card);
    box-shadow: 0 4px 14px rgba(0,0,0,0.18);
  }
  .card--contact { left: 290px; top: 29px; }
  .card--services { left: 24px; top: 559px; }

  .scene-art {
    position: absolute; background: var(--art); border-radius: 4px;
  }
  .card--contact .scene-art { left: 147px; top: 48px; width: 609px; height: 168px; }
  .card--services .scene-art { left: 113px; top: 97px; width: 680px; height: 188px; }

  .rule { position: absolute; left: 0; width: 100%; height: 3px; background: var(--rule); }
  .rule--top { top: 259px; }
  .rule--bottom { top: 325px; }
  .name-band {
    position: absolute; left: 0; top: 270px; width: 100%; height: 49px;
    background: var(--band);
  }
  .company-name {
    position: absolute; left: 405px; top: 0; transform: translateX(-50%);
    font-weight: 700; font-size: 41px; line-height: 49px; white-space: nowrap;
  }

  .holder-name {
    position: absolute; right: 518px; top: 414px;
    font-weight: 700; font-size: 29px; white-space: nowrap;
  }
  .divider {
    position: absolute; left: 400px; top: 379px; width: 1px; height: 79px;
    background: var(--rule); opacity: .7;
  }
  .contact-line {
    position: absolute; left: 426px; display: flex; align-items: center; gap: 10px;
    font-size: 28px; white-space: nowrap;
  }
  .contact-line--phone { top: 377px; font-weight: 600; }
  .contact-line--mail { top: 424px; }
  .contact-line svg { width: 26px; height: 26px; flex: none; }

  .services-title {
    position: absolute; left: 0; width: 100%; top: 352px; text-align: center;
    font-weight: 700; font-size: 30px;
  }
  .services-list {
    position: absolute; left: 0; width: 100%; text-align: center;
    font-size: 29px; white-space: nowrap;
  }
  .services-list--fr { top: 405px; }
  .services-list--en { top: 446px; }
</style>
</head>
<body>
<main class="canvas">
  <section class="card card--contact">
    <div class="scene-art" role="img" aria-label="Line drawing of mountains, a chalet and a hot tub"></div>
    <div class="rule rule--top"></div>
    <div class="name-band"><span class="company-name">58 BAINS</span></div>
    <div class="rule rule--bottom"></div>
    <p class="holder-name">Lucien Marchetti</p>
    <div class="divider"></div>
    <p class="contact-line contact-line--phone">
      <svg viewBox="0 0 24 24" aria-hidden="true"><circle cx="12" cy="12" r="10.5" fill="none" stroke="#fff" stroke-width="1.6"/><path d="M8.5 6.5l2 2.6-1.3 1.4c.8 1.7 2.1 3 3.8 3.8l1.4-1.3 2.6 2-1.2 2c-4.6-.5-8.3-4.2-8.8-8.8z" fill="#fff"/></svg>
      +33 (0)6 71 58 29 64
    </p>
    <p class="contact-line contact-line--mail">
      <svg viewBox="0 0 24 24" aria-hidden="true"><path d="M3 9l9-5 9 5v10H3z" fill="#fff"/><path d="M3 9l9 6 9-6" fill="none" stroke="#22a3f4" stroke-width="1.6"/></svg>
      lucimarch@examplemail.net
    </p>
  </section>

  <section class="card card--services">
    <div class="scene-art" role="img" aria-label="Line drawing of mountains, a chalet and a hot tub"></div>
    <h2 class="services-title">SPAS SERVICES</h2>
    <p class="services-list services-list--fr">•Entretien &nbsp;•traitement eau &nbsp;•nettoyage</p>
    <p class="services-list services-list--en">•Maintenance &nbsp;•water treatment &nbsp;•cleaning.</p>
  </section>
</main>
</body>
</html>
```